Harbor Loom Floors Letterhead

Letterhead used for business reasons. It must be editable and easy to use.

Address is 2715 W. Pelican Lane Englewood FL 34187 - 941.382.6519

```html
<!DOCTYPE html>
<html lang="en">
<head>
<meta charset="utf-8">
<title>Harbor Loom Floors Letterhead</title>
<link rel="stylesheet" href="https://fonts.googleapis.com/css2?family=Lato:wght@400;700&family=Montserrat:wght@400&family=Tangerine:wght@700&display=swap">
<style>
  :root {
    --brand-orange: #e08a2a;
    --brand-taupe: #978c87;
    --ink: #1a1a1a;
    --contact-ink: #333333;
    --paper: #ffffff;
    --backdrop: #e6e6e6;
  }
  * { box-sizing: border-box; margin: 0; padding: 0; }
  html, body {
    width: 1200px; height: 1079px; overflow: hidden;
    background: var(--backdrop);
  }
  .letterhead {
    position: absolute; left: 327px; top: 126px;
    width: 595px; height: 842px;
    background: var(--paper);
    font-family: "Lato", sans-serif;
    color: var(--ink);
  }
  .brand-name {
    position: absolute; left: 30px; top: 34px; width: 150px;
    font-family: "Lato", sans-serif; font-weight: 400;
    font-size: 24px; line-height: 28px;
    color: var(--brand-orange);
  }
  .contact-block {
    position: absolute; left: 431px; top: 65px;
    border-left: 1.5px solid var(--brand-orange);
    padding-left: 19px; height: 44px;
    font-family: "Montserrat", sans-serif; font-size: 10.5px; line-height: 14px;
    color: var(--contact-ink);
  }
  .contact-address { margin-top: -1px; }
  .contact-phone { display: flex; align-items: center; gap: 5px; margin-top: 8px; margin-left: -2px; }
  .contact-phone svg { width: 9px; height: 9px; }
  .letter { position: absolute; left: 29px; width: 536px; font-size: 12px; line-height: 14px; }
  .letter-date { top: 208px; font-size: 12.5px; }
  .recipient { top: 238px; }
  .recipient-company { top: 296px; }
  .salutation { top: 366px; font-weight: 700; font-size: 15px; }
  .letter-body { top: 416px; font-size: 11.6px; line-height: 13.2px; text-align: justify; }
  .letter-body p + p { margin-top: 13.5px; }
  .closing { top: 656px; }
  .signature {
    top: 718px; font-family: "Tangerine", cursive; font-weight: 700;
    font-size: 34px; line-height: 34px;
  }
  .footer-band { position: absolute; left: 0; bottom: 0; width: 595px; height: 17px; }
</style>
</head>
<body>
  <main class="letterhead">
    <div class="brand-name">Harbor Loom Floors</div>

    <div class="contact-block">
      <div class="contact-address">2715 W. Pelican Lane<br>Englewood FL 34187</div>
      <div class="contact-phone">
        <svg viewBox="0 0 24 24" aria-hidden="true"><path fill="var(--brand-orange)" d="M6.6 10.8a15.1 15.1 0 0 0 6.6 6.6l2.2-2.2c.3-.3.7-.4 1-.2 1.1.4 2.3.6 3.6.6.6 0 1 .4 1 1V20c0 .6-.4 1-1 1A17 17 0 0 1 3 4c0-.6.4-1 1-1h3.5c.6 0 1 .4 1 1 0 1.3.2 2.5.6 3.6.1.3 0 .7-.2 1z"/></svg>
        <span>941.382.6519</span>
      </div>
    </div>

    <div class="letter letter-date">January-03-2020</div>
    <div class="letter recipient">Mr. Alan Reyes<br>President</div>
    <div class="letter recipient-company">Crestline Partners<br>123 Street Name, Suite# 10<br>City, State, 120023</div>
    <div class="letter salutation">Dear Mr. Reyes</div>

    <div class="letter letter-body">
      <p>Lorem ipsum dolor sit amet, consectetur adipiscing elit, sed do eiusmod tempor incididunt ut labore et dolore magna aliqua. Ut enim ad minim veniam, quis nostrud exercitation ullamco laboris nisi ut aliquip ex ea commodo consequat. Duis aute irure dolor in reprehenderit in voluptate velit esse cillum dolore eu fugiat nulla pariatur.</p>
      <p>Lorem ipsum dolor sit amet, consectetur adipiscing elit, sed do eiusmod tempor incididunt ut labore et dolore magna aliqua. Ut enim ad minim veniam, quis nostrud exercitation ullamco laboris nisi ut aliquip ex ea commodo consequat. Duis aute irure dolor in reprehenderit in voluptate velit esse cillum dolore eu fugiat nulla pariatur.</p>
      <p>Lorem ipsum dolor sit amet, consectetur adipiscing elit, sed do eiusmod tempor incididunt ut labore et dolore magna aliqua. Ut enim ad minim veniam, quis nostrud exercitation ullamco laboris nisi ut aliquip ex ea commodo consequat.</p>
      <p>Excepteur sint occaecat cupidatat non proident, sunt in culpa qui officia deserunt mollit anim id est laborum. re et dolore magnam aliquam quaerat voluptatem.</p>
    </div>

    <div class="letter closing">Regards</div>
    <div class="letter signature">Daniel Hart</div>

    <svg class="footer-band" viewBox="0 0 595 17" preserveAspectRatio="none" aria-hidden="true">
      <polygon points="0,0 269,0 289,17 0,17" fill="var(--brand-orange)"/>
      <polygon points="278,0 595,0 595,17 297,17" fill="var(--brand-taupe)"/>
    </svg>
  </main>
</body>
</html>
```